Site for entrepreneurs/small businesses needs Logo, Homepage

Looking for a logo, either an icon, or stylized text, or a combination of both, and a home page design which fits with it. The logo will be for use on the public website as well as for printed collateral (business cards, post cards, brochures and various other marketing materials).

The site is called Orbitwell (Orbitwell.example). This is to be a national, and eventually an international brand. The new service will provide an easy-to-use platform for entrepreneurs to build their business and web presence together in an integrated way which allows them to focus on their core competency.

The site/service will be dead-simple to use, A/B/C, 1/2/3. We will want some sort of "Get started for FREE" promotional space to collect the person's email address with multiple points of interest which guide the user back to this one call to action: sign up for free. We will feature editorial/blog stories, customer testimonials, and present several key features the the reader just can't live without if they are starting a new business.

Criteria:
* Refer to our comparable sites/logos in the design document attached
* Incorporate our color scheme (but complementary colors welcome)
* No Serif fonts!
* No photo-realistic elements for logo
* Logo must present well in gray scale and/or black/white (for printed materials)
* Strokes/borders that are wider to promote simplicity (vs. thin/precise lines which promote technical complexity)

Inspirations:
* Creative/Custom (but legible) fonts
* Excitement, energetic, jumping for joy
* Karate / Ninja / Power / Precision
* Dance Moves
* Regional influences: California, Silicon Valley, West Coast, Surf City, Beaches, Sunset
* Simple/easy, no-brainer solutions

Target Market(s)

Small Businesses / Entrepreneurs

Logo Text

Orbitwell or Orbitwell.example

Number of Pages Required

1 page

Font styles to use
Sans Serif
Decorative

Requirements
Must have
• See the attached style guide (PDF)

```html
<!DOCTYPE html>
<html lang="en">
<head>
<meta charset="utf-8">
<title>Orbitwell — Platform for entrepreneurs</title>
<link href="https://fonts.googleapis.com/css2?family=Fira+Sans:wght@500;600;700&family=Open+Sans:wght@400;600;700&display=swap" rel="stylesheet">
<style>
:root{
  --navy:#1d2a4a;
  --hero-top:#1a5a92;
  --hero-bottom:#2479bd;
  --form-blue:#1a6fd0;
  --orange:#e0600c;
  --link-blue:#1f6fc4;
  --sky:#45a6e6;
  --sky-light:#7cc4f2;
  --pale:#eaf3fa;
  --footer:#1b5d9a;
  --text:#555b66;
  --white:#ffffff;
}
*{box-sizing:border-box;margin:0;padding:0}
html,body{width:1200px;height:3403px;overflow:hidden}
body{position:relative;font-family:"Open Sans",Arial,sans-serif;color:var(--text);background:var(--white)}
.abs{position:absolute}
h2.section-title{position:absolute;left:0;width:1200px;text-align:center;font-family:"Fira Sans",Arial,sans-serif;font-weight:600;font-size:31px;color:var(--navy)}
.title-rule{position:absolute;left:570px;width:60px;height:2px;background:#9aa3b3}
.btn{position:absolute;display:flex;align-items:center;justify-content:center;border-radius:8px;font-family:"Open Sans",Arial,sans-serif;font-weight:600;color:var(--white)}
.btn-orange{background:var(--orange)}
/* hero */
.hero{position:absolute;left:0;top:0;width:1200px;height:646px;background:linear-gradient(180deg,var(--hero-top),var(--hero-bottom));overflow:hidden}
.brand{position:absolute;left:102px;top:36px;display:flex;align-items:center;gap:8px;font-family:"Fira Sans",Arial,sans-serif;font-weight:700;font-size:34px;color:var(--white)}
.brand-dot{width:10px;height:10px;border-radius:50%;background:var(--orange)}
.nav{position:absolute;top:48px;left:537px;display:flex;gap:24px;font-size:14px;color:var(--white);letter-spacing:.3px}
.lang{position:absolute;left:1032px;top:44px;width:70px;height:28px;border:1.5px solid var(--white);color:var(--white);font-size:12px;display:flex;align-items:center;justify-content:center}
.hero-title{position:absolute;left:102px;top:184px;font-family:"Fira Sans",Arial,sans-serif;font-weight:600;font-size:41px;line-height:53px;color:var(--white)}
.btn-outline{left:102px;top:376px;width:127px;height:45px;border:2px solid var(--white);border-radius:10px;font-size:18px}
.rocket{position:absolute;left:664px;top:118px;width:46px;height:130px;border-radius:23px;background:linear-gradient(180deg,rgba(255,255,255,.35),rgba(255,255,255,.05))}
.signup{position:absolute;left:714px;top:159px;width:386px;height:306px;background:var(--form-blue);border:2px solid rgba(255,255,255,.8)}
.signup h3{position:absolute;top:36px;width:100%;text-align:center;font-family:"Fira Sans",Arial,sans-serif;font-weight:600;font-size:23px;color:var(--white)}
.field{position:absolute;height:36px;background:var(--white);border-radius:2px;font-size:11px;color:#666;padding:0 12px;display:flex;align-items:center}
.hero-arrow{position:absolute;top:285px}
.dots{position:absolute;left:604px;top:538px;display:flex;gap:4px}
.dots span{width:8px;height:8px;border-radius:50%;border:1.5px solid var(--white)}
.dots span:first-child{background:var(--white)}
.cloud-band{position:absolute;left:0;top:500px;width:1200px;height:146px;background:linear-gradient(180deg,rgba(255,255,255,0),rgba(255,255,255,.85) 45%,#fff 75%)}
/* problems */
.problem-art{position:absolute;left:150px;top:800px;width:360px;height:360px;border-radius:50%;background:#a9d9db}
.problem-head{position:absolute;left:637px;top:843px;font-family:"Fira Sans",Arial,sans-serif;font-weight:600;font-size:19px;line-height:30px;color:var(--link-blue)}
.problem-text{position:absolute;left:637px;top:922px;width:463px;font-size:12.5px;line-height:29px;text-align:justify}
/* features */
.features{position:absolute;left:0;top:1259px;width:1200px;height:623px;background:var(--pale)}
.feature-img{position:absolute;width:254px;height:254px;border-radius:50%;border:4px solid var(--link-blue)}
.feature-cap{position:absolute;width:300px;text-align:center;font-size:14px;line-height:25px;color:#333}
/* blog */
.post{position:absolute;top:2082px;width:227px}
.post-img{width:227px;height:175px}
.post h4{margin-top:26px;font-family:"Fira Sans",Arial,sans-serif;font-weight:600;font-size:15.5px;color:var(--link-blue)}
.post-meta{margin-top:9px;font-size:11.5px;color:#333;display:flex;align-items:center;gap:6px}
.post p{margin-top:6px;font-size:11.5px;line-height:18px}
.post .more{margin-top:7px;font-size:11.5px;font-weight:700;color:var(--orange)}
/* testimonials */
.testimonials{position:absolute;left:0;top:2517px;width:1200px;height:545px;background:linear-gradient(180deg,var(--sky),var(--sky-light) 70%,#dff0fb);overflow:hidden}
.testimonials h2{color:var(--white);top:80px}
.testimonial-art{position:absolute;left:200px;top:160px;width:300px;height:330px;border-radius:150px 150px 60px 60px;background:linear-gradient(180deg,rgba(255,255,255,.15),rgba(255,255,255,.75))}
.quote{position:absolute;left:522px;top:180px;width:578px;font-size:13px;line-height:29px;color:var(--white)}
.quote-name{position:absolute;left:522px;top:308px;font-size:13px;font-weight:700;color:var(--white)}
.quote-arrow{position:absolute;left:1142px;top:218px}
/* footer */
.footer{position:absolute;left:0;top:3062px;width:1200px;height:341px;background:var(--footer);color:var(--white)}
.footer h5{position:absolute;top:60px;font-family:"Fira Sans",Arial,sans-serif;font-weight:600;font-size:21px;letter-spacing:.5px}
.footer .col{position:absolute;top:104px;font-size:12px;line-height:25px}
.footer .field{width:209px;height:40px;border-radius:3px}
.footer-rule{position:absolute;left:102px;top:283px;width:998px;height:1px;background:rgba(255,255,255,.35)}
.copyright{position:absolute;left:102px;top:302px;font-size:11.5px}
.socials{position:absolute;left:1000px;top:303px;display:flex;gap:14px}
.socials span{width:12px;height:12px;border-radius:50%;background:var(--white)}
</style>
</head>
<body>

<header class="hero">
  <div class="rocket" role="img" aria-label="Illustration of a rocket launching with stars"></div>
  <div class="brand"><span class="brand-dot"></span>Orbitwell</div>
  <nav class="nav"><span>WHO ARE WE</span><span>BLOG</span><span>TESTIMONIALS</span><span>FEATURES</span><span>CONTACT</span></nav>
  <div class="lang">ENG &#8964;</div>

  <h1 class="hero-title">Platform for entrepreneurs<br>to build their business &amp;<br>web presence</h1>
  <div class="btn btn-outline">Our Work</div>

  <form class="signup">
    <h3>Get Started for FREE</h3>
    <div class="field" style="left:34px;top:99px;width:152px">First Name</div>
    <div class="field" style="left:199px;top:99px;width:152px">Last Name</div>
    <div class="field" style="left:34px;top:157px;width:317px;justify-content:space-between">Enter You Email Address
      <svg width="14" height="10" viewBox="0 0 14 10"><rect x="1" y="1" width="12" height="8" fill="none" stroke="#666" stroke-width="1.3"/><path d="M1 1l6 5 6-5" fill="none" stroke="#666" stroke-width="1.3"/></svg></div>
    <div class="btn btn-orange" style="left:112px;top:228px;width:162px;height:38px;font-size:15px">Sign up for free</div>
  </form>

  <svg class="hero-arrow" style="left:30px" width="22" height="40" viewBox="0 0 22 40"><path d="M19 2L3 20l16 18" fill="none" stroke="#fff" stroke-width="3"/></svg>
  <svg class="hero-arrow" style="left:1148px" width="22" height="40" viewBox="0 0 22 40"><path d="M3 2l16 18L3 38" fill="none" stroke="#fff" stroke-width="3"/></svg>

  <div class="cloud-band" role="img" aria-label="Decorative band of white clouds"></div>
  <div class="dots"><span></span><span></span><span></span><span></span></div>
</header>

<section class="problems">
  <h2 class="section-title" style="top:700px">Problems We Solve</h2>
  <div class="title-rule" style="top:756px"></div>
  <div class="problem-art" role="img" aria-label="Illustration of an excited entrepreneur jumping with a briefcase and papers"></div>
  <div class="problem-head">TYPICAL PROBLEMS AND CHALLENGES<br>ENTREPRENEURS FACE:</div>
  <p class="problem-text">"Vero eos et accusamus et iusto odio dignissimos ducimus qui blanditiis praesentium voluptatum deleniti atque corrupti quos dolores et quas moles tias excepturi sint occaecati cupiditate non provident, similique sunt in culpa qui officia deserunt mollitia animi, id est laborum et dolorum fuga. Et harum quidem rerum facilis est et expedita distinctio libero" .</p>
  <div class="btn btn-orange" style="left:637px;top:1098px;width:121px;height:40px;font-size:14px">Read More</div>
</section>

<section class="features">
  <h2 class="section-title" style="top:104px">Our Features</h2>
  <div class="title-rule" style="top:159px"></div>
  <div class="feature-img" role="img" aria-label="Illustration of a businessman leaping over a city skyline" style="left:132px;top:211px;background:linear-gradient(180deg,#f4efe6 0%,#e7664a 55%,#3d5a8a 100%)"></div>
  <div class="feature-img" role="img" aria-label="Illustration of a businessman crossing a finish line ribbon" style="left:497px;top:211px;background:linear-gradient(180deg,#ffffff 0%,#f4f4f4 55%,#e04a3a 100%)"></div>
  <div class="feature-img" role="img" aria-label="Illustration of a caped businessman flying upward with arrows" style="left:840px;top:211px;background:linear-gradient(160deg,#2b8fd6,#56b2ea)"></div>
  <p class="feature-cap" style="left:109px;top:490px">Sed ut perspiciatis unde omniste natu<br>sit voluptatem acsantium</p>
  <p class="feature-cap" style="left:474px;top:490px">Sed ut perspiciatis unde omniste natu<br>sit voluptatem acsantium</p>
  <p class="feature-cap" style="left:817px;top:490px">Sed ut perspiciatis unde omniste natu<br>sit voluptatem acsantium</p>
</section>

<section class="blog">
  <h2 class="section-title" style="top:1980px">Our Blog</h2>
  <div class="title-rule" style="top:2036px"></div>

  <article class="post" style="left:102px">
    <div class="post-img" role="img" aria-label="Illustration of a busy worker at a desk with flying papers" style="background:linear-gradient(180deg,#cfe3f3,#7fb0d8)"></div>
    <h4>Lorem Ipsum Is Simple</h4>
    <div class="post-meta"><svg width="11" height="11" viewBox="0 0 11 11"><rect x="1" y="2" width="9" height="8" fill="none" stroke="#e0600c" stroke-width="1.4"/><path d="M1 4.5h9" stroke="#e0600c" stroke-width="1.4"/></svg>May 25, 2018 &nbsp;&nbsp;&nbsp;<svg width="12" height="10" viewBox="0 0 12 10"><path d="M1 1h10v6H5l-3 2V7H1z" fill="none" stroke="#e0600c" stroke-width="1.3"/></svg>4</div>
    <p>Similique sunt in culpa qui officiae des runt mollitia animi, id est laborum et</p>
    <div class="more">Read More</div>
  </article>

  <article class="post" style="left:358px">
    <div class="post-img" role="img" aria-label="Illustration of a woman jumping in an office" style="background:linear-gradient(180deg,#eef1f6,#d9dde6 70%,#c9a9a4)"></div>
    <h4>Lorem Ipsum Is Simple</h4>
    <div class="post-meta"><svg width="11" height="11" viewBox="0 0 11 11"><rect x="1" y="2" width="9" height="8" fill="none" stroke="#e0600c" stroke-width="1.4"/><path d="M1 4.5h9" stroke="#e0600c" stroke-width="1.4"/></svg>May 25, 2018 &nbsp;&nbsp;&nbsp;<svg width="12" height="10" viewBox="0 0 12 10"><path d="M1 1h10v6H5l-3 2V7H1z" fill="none" stroke="#e0600c" stroke-width="1.3"/></svg>4</div>
    <p>Similique sunt in culpa qui officiae des runt mollitia animi, id est laborum et</p>
    <div class="more">Read More</div>
  </article>

  <article class="post" style="left:614px">
    <div class="post-img" role="img" aria-label="Illustration of a businessman climbing a rising line on a grid" style="background:linear-gradient(180deg,#ffffff,#e6e6e6);border:1px solid #e3e3e3"></div>
    <h4>Lorem Ipsum Is Simple</h4>
    <div class="post-meta"><svg width="11" height="11" viewBox="0 0 11 11"><rect x="1" y="2" width="9" height="8" fill="none" stroke="#e0600c" stroke-width="1.4"/><path d="M1 4.5h9" stroke="#e0600c" stroke-width="1.4"/></svg>May 25, 2018 &nbsp;&nbsp;&nbsp;<svg width="12" height="10" viewBox="0 0 12 10"><path d="M1 1h10v6H5l-3 2V7H1z" fill="none" stroke="#e0600c" stroke-width="1.3"/></svg>4</div>
    <p>Similique sunt in culpa qui officiae des runt mollitia animi, id est laborum et</p>
    <div class="more">Read More</div>
  </article>

  <article class="post" style="left:870px">
    <div class="post-img" role="img" aria-label="Illustration of a businessman over a rising stock chart" style="background:linear-gradient(180deg,#1e5fae,#3c86cf)"></div>
    <h4>Lorem Ipsum Is Simple</h4>
    <div class="post-meta"><svg width="11" height="11" viewBox="0 0 11 11"><rect x="1" y="2" width="9" height="8" fill="none" stroke="#e0600c" stroke-width="1.4"/><path d="M1 4.5h9" stroke="#e0600c" stroke-width="1.4"/></svg>May 25, 2018 &nbsp;&nbsp;&nbsp;<svg width="12" height="10" viewBox="0 0 12 10"><path d="M1 1h10v6H5l-3 2V7H1z" fill="none" stroke="#e0600c" stroke-width="1.3"/></svg>4</div>
    <p>Similique sunt in culpa qui officiae des runt mollitia animi, id est laborum et</p>
    <div class="more">Read More</div>
  </article>
</section>

<section class="testimonials">
  <h2 class="section-title">Testimonials</h2>
  <div class="title-rule" style="top:133px;background:rgba(255,255,255,.8)"></div>
  <div class="abs" role="img" aria-label="Decorative band of white clouds" style="left:0;top:400px;width:1200px;height:145px;background:linear-gradient(180deg,rgba(255,255,255,0),rgba(255,255,255,.9))"></div>
  <div class="testimonial-art" role="img" aria-label="Illustration of a person with a laptop sitting on a cloud"></div>
  <p class="quote">" Sed ut perspiciatis unde omnis iste natus error sit voluptatem accusantium doloremque lau dantium, totam rem aperiam, eaque ipsa quae ab illo inventore veritatis et quasi ar chitecto beatae vitae dicta sunt explicabo. Nemo enim ipsam voluptatem quia voluptas sit aspernatur aut odit aut fugit, sed quia con ipsum quia dolor sit. "</p>
  <div class="quote-name">- Sam Rivera</div>
  <svg class="quote-arrow" width="40" height="18" viewBox="0 0 40 18"><path d="M2 9h34M28 2l8 7-8 7" fill="none" stroke="rgba(255,255,255,.7)" stroke-width="3"/></svg>
</section>

<footer class="footer">
  <h5 style="left:102px">ABOUT</h5>
  <p class="col" style="left:102px;width:240px;line-height:24px">Lorem ipsum dolor sit amet, consectetur adipisicing elit, sed do eiusmod tempor incididunt ut labore et dolore magna to aliqua veniam.</p>

  <h5 style="left:390px">CONTACT US</h5>
  <div class="col" style="left:390px">
    <div style="display:flex;gap:10px"><svg width="10" height="14" viewBox="0 0 10 14" style="margin-top:5px"><path d="M5 13S1 8 1 5a4 4 0 018 0c0 3-4 8-4 8z" fill="#fff"/><circle cx="5" cy="5" r="1.5" fill="#1b5d9a"/></svg><span>Orbitwell, Lorem Ipsum,<br>Lorem Ipsum Is Simply Dummy</span></div>
    <div style="display:flex;gap:10px;align-items:center"><svg width="11" height="11" viewBox="0 0 11 11"><path d="M2 1l2 2-1 1.5a6 6 0 003.5 3.5L8 7l2 2-1.5 1.5C5 10 1 6 .5 2.5z" fill="#fff"/></svg>(+1) 555 010 0199</div>
    <div style="display:flex;gap:10px;align-items:center"><svg width="12" height="9" viewBox="0 0 12 9"><rect width="12" height="9" fill="#fff"/><path d="M0 0l6 5 6-5" fill="none" stroke="#1b5d9a" stroke-width="1.2"/></svg>support@orbitwell.example</div>
  </div>

  <h5 style="left:678px">USEFUL LINKS</h5>
  <div class="col" style="left:678px">&gt;&gt; Why Orbitwell<br>&gt;&gt; Blog<br>&gt;&gt; Testimonials<br>&gt;&gt; Features</div>

  <h5 style="left:891px">FOR NEWSLETTER</h5>
  <div class="field" style="left:891px;top:102px">Your Name</div>
  <div class="field" style="left:891px;top:160px">Email - Address</div>
  <div class="btn btn-orange" style="left:891px;top:217px;width:135px;height:36px;border-radius:3px;font-size:13px">Subscribe Now</div>

  <div class="footer-rule"></div>
  <div class="copyright">Copyrights © 2018 Orbitwell. All Rights Reserved.</div>
  <div class="socials" aria-label="Social links"><span></span><span></span><span></span><span></span></div>
</footer>

</body>
</html>
```